VFX Company Business Card Design Project

The Kestrel Works is a decentralized Visual Effects Studio servicing the television and feature film industries.
Project Brief:
Take our logo that was previously designed on Pencil Harbor and make a double sided business card.
Requirements:
- Card MUST be double sided.
- Front of card MUST have the yellow part of our logo against the dark grey background.
- Back of card is completely up to the designer.
- Back of card must include the complete company logo.
Please follow these File Preparation guidelines:
http://printnook.ca/infopage?file=filetype_en&s=PrintNook_new&lang=en
Business

```html
<!DOCTYPE html>
<html lang="en">
<head>
<meta charset="utf-8">
<title>The Kestrel Works – Business Cards</title>
<link rel="stylesheet" href="https://fonts.googleapis.com/css2?family=Jost:wght@400;500;600&display=swap">
<style>
  :root {
    --backdrop: #7a4020;
    --card-dark: #2b2b2b;
    --accent-yellow: #fec52a;
    --ink-light: #eef0e8;
    --ink-grey: #5f6b6e;
    --swoosh-grey: #5f6b6e;
    --panel-light: #eef0e8;
    --ink-dark: #2b2b2b;
  }
  * { margin: 0; padding: 0; box-sizing: border-box; }
  html, body {
    width: 1200px; height: 734px; overflow: hidden;
    background: var(--backdrop);
    font-family: "Jost", "Helvetica Neue", Arial, sans-serif;
  }
  .stage { position: relative; width: 1200px; height: 734px; }
  .card {
    position: absolute; width: 523px; height: 299px;
    background: var(--card-dark); overflow: hidden;
    color: var(--ink-light);
  }
  .card--front-mark { left: 68px; top: 43px; }
  .card--contact   { left: 628px; top: 48px; }
  .card--lockup    { left: 64px; top: 381px; }
  .card--wordmark  { left: 622px; top: 387px; }

  .brand-name { font-weight: 600; letter-spacing: -0.5px; white-space: nowrap; line-height: 1; }
  .tagline { font-weight: 400; letter-spacing: 7px; color: var(--ink-grey); white-space: nowrap; }

  /* Front */
  .front-mark {
    position: absolute; inset: 0;
    display: flex; align-items: center; justify-content: center; gap: 18px;
  }
  .front-mark .dot { width: 54px; height: 54px; border-radius: 50%; background: var(--accent-yellow); }
  .front-mark .brand-name { color: var(--accent-yellow); font-size: 40px; }

  /* Contact card */
  .swoosh { position: absolute; inset: 0; }
  .contact-brand { position: absolute; left: 27px; top: 48px; }
  .contact-brand .brand-name { font-size: 38px; color: var(--ink-light); }
  .contact-brand .tagline { font-size: 15px; letter-spacing: 6px; margin-top: 6px; }
  .address { position: absolute; left: 29px; top: 150px; font-size: 14px; letter-spacing: 0.3px; }
  .person { position: absolute; left: 29px; top: 224px; }
  .person-name { font-size: 19px; font-weight: 400; }
  .person-title { font-size: 12px; margin-top: 2px; }
  .contact-list {
    position: absolute; right: 31px; top: 202px; list-style: none;
    color: var(--ink-dark); font-size: 13px; text-align: right;
  }
  .contact-list li { height: 22.5px; display: flex; align-items: center; justify-content: flex-end; gap: 6px; }
  .contact-list svg { width: 10px; height: 10px; fill: var(--ink-dark); }

  /* Lockup back */
  .lockup {
    position: absolute; left: 0; right: 0; top: 112px;
    display: flex; align-items: center; justify-content: center; gap: 18px;
  }
  .lockup .dot { width: 46px; height: 46px; border-radius: 50%; background: var(--accent-yellow); }
  .lockup .brand-name { font-size: 34px; color: var(--ink-light); }
  .lockup .tagline { font-size: 13px; letter-spacing: 5px; margin-top: 6px; }

  /* Wordmark back */
  .wordmark {
    position: absolute; left: 0; right: 0; top: 98px; text-align: center;
  }
  .wordmark .brand-name { font-size: 52px; color: var(--ink-light); }
  .wordmark .tagline { font-size: 20px; letter-spacing: 8px; margin-top: 10px; }

  .web {
    position: absolute; left: 0; right: 0; top: 256px; text-align: center;
    font-size: 17px; letter-spacing: 3px; color: var(--ink-light);
  }
</style>
</head>
<body>
<main class="stage">

  <section class="card card--front-mark" aria-label="Card front">
    <div class="front-mark">
      <span class="dot"></span>
      <span class="brand-name">The Kestrel Works</span>
    </div>
  </section>

  <section class="card card--contact" aria-label="Contact card">
    <svg class="swoosh" viewBox="0 0 523 299" preserveAspectRatio="none" aria-hidden="true">
      <path d="M455 0 Q440 210 155 299 L523 299 L523 0 Z" fill="var(--swoosh-grey)"/>
      <path d="M523 32 Q480 228 172 299 L523 299 Z" fill="var(--panel-light)"/>
    </svg>
    <div class="contact-brand">
      <div class="brand-name">The Kestrel Works</div>
      <div class="tagline">VIRTUAL STUDIO</div>
    </div>
    <p class="address">00, Complex name, City, State 0042</p>
    <div class="person">
      <p class="person-name">Your Name</p>
      <p class="person-title">Title</p>
    </div>
    <ul class="contact-list">
      <li><svg viewBox="0 0 10 10"><path d="M2 0.5 L3.6 2.6 L2.7 3.6 Q3.8 6 6.4 7.3 L7.4 6.4 L9.5 8 L8.3 9.5 Q1 7.5 0.5 1.7 Z"/></svg>0987 654321</li>
      <li><svg viewBox="0 0 10 10"><rect x="2.5" y="0.5" width="5" height="9" rx="1"/></svg>0987 654321</li>
      <li><svg viewBox="0 0 10 10"><path d="M0.5 2 H9.5 V8.5 H0.5 Z M1 2.5 L5 5.6 L9 2.5" stroke="var(--panel-light)" stroke-width="0.8"/></svg>info@kestrelworks.com</li>
      <li><svg viewBox="0 0 10 10"><circle cx="5" cy="5" r="4.5"/><path d="M0.5 5 H9.5 M5 0.5 V9.5" stroke="var(--panel-light)" stroke-width="0.8"/></svg>www.kestrelworks.com</li>
    </ul>
  </section>

  <section class="card card--lockup" aria-label="Card back with logo lockup">
    <div class="lockup">
      <span class="dot"></span>
      <div>
        <div class="brand-name">The Kestrel Works</div>
        <div class="tagline">VIRTUAL STUDIO</div>
      </div>
    </div>
    <p class="web">www.kestrelworks.com</p>
  </section>

  <section class="card card--wordmark" aria-label="Card back with wordmark">
    <div class="wordmark">
      <div class="brand-name">The Kestrel Works</div>
      <div class="tagline">VIRTUAL STUDIO</div>
    </div>
    <p class="web">www.kestrelworks.com</p>
  </section>

</main>
</body>
</html>
```